Business Card Design

We require a business card design for a law firm, our signature colours are maroon and cream. Our slogan is "From our family to yours", we would like the cards to be professional however feminine at the same time.

Industry/Entity Type

Business

Contact Information for Business Card

Helena Drace & Associates Lawyers & Conveyancers, Helena Drace LL.B. Principal Solicitor, 17 Kellow Street, Marrick NSW 2299

Logo styles of interest
Emblem Logo
Abstract Logo
Wordmark Logo

```html
<!DOCTYPE html>
<html lang="en">
<head>
<meta charset="utf-8">
<title>Helena Drace &amp; Associates – Business Card</title>
<link rel="stylesheet" href="https://fonts.googleapis.com/css2?family=Tinos:wght@400;700&display=swap">
<style>
  :root {
    --maroon: #a8063a;
    --maroon-deep: #8e0430;
    --cream: #d9c9a3;
    --cream-soft: #e6dabb;
    --ink: #141414;
    --paper: #ffffff;
    --backdrop: #e9e7e4;
  }
  * { box-sizing: border-box; margin: 0; padding: 0; }
  html, body {
    width: 1200px;
    height: 900px;
    overflow: hidden;
    background: var(--backdrop);
    font-family: "Tinos", "Times New Roman", serif;
  }
  .canvas {
    width: 1200px;
    height: 900px;
    display: flex;
    flex-direction: column;
    align-items: center;
    justify-content: center;
    gap: 48px;
  }
  .card {
    position: relative;
    width: 640px;
    height: 391px;
    overflow: hidden;
    box-shadow: 0 6px 18px rgba(0,0,0,0.18);
  }

  /* Back of card */
  .card-back {
    background: linear-gradient(160deg, var(--maroon) 0%, var(--maroon-deep) 100%);
    color: var(--cream);
  }
  .back-mark {
    position: absolute;
    left: 120px;
    top: 118px;
    display: flex;
    align-items: center;
    gap: 22px;
  }
  .back-mark__circle {
    width: 78px;
    height: 78px;
    border-radius: 50%;
    background: var(--cream);
    flex: none;
  }
  .back-mark__name {
    font-size: 30px;
    line-height: 1.1;
    font-weight: 400;
    color: var(--cream);
  }
  .back-mark__practice {
    font-size: 21px;
    font-weight: 400;
    color: var(--cream);
    margin-top: 4px;
  }
  .back-rule {
    position: absolute;
    left: 120px;
    right: 60px;
    top: 232px;
    height: 1px;
    background: var(--cream);
  }
  .back-slogan {
    position: absolute;
    left: 220px;
    top: 248px;
    font-size: 17px;
    letter-spacing: 0.34em;
    text-transform: uppercase;
    color: var(--cream);
  }

  /* Front of card */
  .card-front {
    background: linear-gradient(180deg, var(--paper) 0%, #f3f3f3 100%);
    color: var(--ink);
  }
  .front-accent {
    position: absolute;
    right: -110px;
    top: 40px;
    width: 330px;
    height: 330px;
    border-radius: 50%;
    background: var(--cream-soft);
  }
  .firm {
    position: absolute;
    left: 52px;
    top: 48px;
    color: var(--maroon);
  }
  .firm__name { font-size: 28px; line-height: 1.1; }
  .firm__practice { font-size: 21px; line-height: 1.2; }
  .contact {
    position: absolute;
    left: 70px;
    top: 150px;
    font-size: 19px;
    line-height: 1.25;
  }
  .contact__name { font-weight: 700; font-size: 23px; }
  .contact__role { margin-bottom: 20px; }
  .contact__lines { margin-bottom: 20px; }
  .contact__label { display: inline-block; width: 56px; }
</style>
</head>
<body>
<main class="canvas">
  <section class="card card-back" aria-label="Card back">
    <div class="back-mark">
      <span class="back-mark__circle" aria-hidden="true"></span>
      <div>
        <p class="back-mark__name">Helena Drace &amp; Associates</p>
        <p class="back-mark__practice">Lawyers &amp; Conveyancers</p>
      </div>
    </div>
    <div class="back-rule" aria-hidden="true"></div>
    <p class="back-slogan">From our family to yours</p>
  </section>

  <section class="card card-front" aria-label="Card front">
    <div class="front-accent" aria-hidden="true"></div>
    <header class="firm">
      <p class="firm__name">Helena Drace &amp; Associates</p>
      <p class="firm__practice">Lawyers &amp; Conveyancers</p>
    </header>
    <div class="contact">
      <p class="contact__name">Helena Drace LL.B.</p>
      <p class="contact__role">Principal Solicitor</p>
      <div class="contact__lines">
        <p><span class="contact__label">Phone</span>5550 123 456</p>
        <p><span class="contact__label">Email</span>info@hdrace.com</p>
      </div>
      <address style="font-style: normal;">
        <p>17 Kellow Street</p>
        <p>Marrick NSW 2299</p>
      </address>
    </div>
  </section>
</main>
</body>
</html>
```